Website Design Request - Management Consulting Firm

We need a Website designed for an IT Management Staffing and Recruiting firm called TRAVENOK based in San Francisco.

The firm is an high-end technology staffing agency. Our focus is on quality and high-caliber candidates rather than quantity.

The website will have two main home pages. One for the recruiter and another on for the candidates.

The website needs to optimize for mobile devices as well.

I have attached few mock-ups that I have done just to show what I am thinking. The UI needs to be very clean, fluid, and it needs to have a modern, rustic, professional feel to it.

Target Market(s)

Technology Manager, Director, VP, CIO of Companies that have $4b-10b dollar revenue. Such as larkspurdwellings.example , https://www.velmorian.example/, quillnet.example, zib.example

Industry/Entity Type

Management Consulting

Number of Pages Required

5+ page

Font styles to use
Sans Serif

Colors
f37122
ffffff

Requirements
Must have
• Please review mock-ups for suggestions
Nice to have
Should not have

```html
<!DOCTYPE html>
<html lang="en">
<head>
<meta charset="utf-8">
<title>TRAVENOK – Project Management Consulting</title>
<link href="https://fonts.googleapis.com/css2?family=Open+Sans:wght@300;400;600&display=swap" rel="stylesheet">
<style>
:root{
  --orange:#f37122;
  --white:#ffffff;
  --ink:#333333;
  --dark:#323232;
  --muted:#9a9a9a;
  --footer:#ebece4;
  --line:#d6d7cf;
}
*{box-sizing:border-box;margin:0;padding:0}
html,body{width:710px;height:1200px;overflow:hidden;background:var(--white)}
body{font-family:"Open Sans",Arial,sans-serif;color:var(--ink);position:relative}
.abs{position:absolute}
.center{text-align:center}

/* header */
.site-header{position:absolute;left:0;top:0;width:710px;height:64px;background:var(--white)}
.brand{position:absolute;left:78px;top:12px}
.brand-name{font-size:30px;font-weight:600;color:var(--orange);letter-spacing:1px;line-height:1}
.brand-tag{font-size:7.5px;color:#222;letter-spacing:.6px;margin-top:4px}
.main-nav a{position:absolute;top:29px;font-size:7px;color:#333;text-decoration:none}

/* hero */
.hero{position:absolute;left:0;top:64px;width:710px;height:273px;
  background:radial-gradient(ellipse at 60% 40%,#5a5a5a 0%,#3a3a3a 55%,#262626 100%)}
.hero-title{position:absolute;top:66px;width:100%;font-size:24px;font-weight:400;color:var(--white)}
.hero-sub{position:absolute;top:104px;width:100%;font-size:8.5px;color:var(--white)}
.email-field{position:absolute;left:162px;top:134px;width:288px;height:25px;background:var(--white);border:1px solid #222;font-size:6px;padding:8px 9px;color:#333}
.btn{background:var(--orange);color:var(--white);font-size:7.5px;text-align:center;text-transform:uppercase}
.hero-btn{position:absolute;left:454px;top:134px;width:94px;height:26px;line-height:26px}
.hero-note{position:absolute;left:164px;top:164px;font-size:5.6px;color:var(--white)}
.hero-note u,.hero-job u{text-decoration:underline}
.hero-job{position:absolute;top:227px;width:100%;font-size:5.6px;color:var(--white)}

/* tabs */
.tab-band{position:absolute;left:0;top:337px;width:710px;height:55px;background:var(--orange)}
.tab{position:absolute;top:17px;font-size:14px;color:rgba(255,255,255,.6)}
.tab.active{color:var(--white)}

/* welcome */
.welcome-title{position:absolute;top:416px;width:100%;font-size:15px}
.welcome-sub{position:absolute;top:447px;width:100%;font-size:8px}
.focus{position:absolute;top:489px;width:170px;text-align:center}
.focus-ring{width:70px;height:70px;border:2px solid var(--orange);border-radius:50%;margin:0 auto;display:flex;align-items:center;justify-content:center}
.focus h3{font-size:14px;font-weight:400;margin-top:11px}
.focus p{font-size:6px;color:var(--muted);line-height:14px;margin-top:10px;padding:0 7px}

/* hiring */
.hiring{position:absolute;left:0;top:680px;width:710px;height:327px;background:var(--dark);color:var(--white)}
.hiring-title{position:absolute;top:30px;width:100%;font-size:15px}
.hiring-sub{position:absolute;top:60px;width:100%;font-size:8px}
.divider{position:absolute;left:356px;top:86px;width:1px;height:210px;background:#555}
.role-title{position:absolute;top:111px;width:200px;text-align:center;font-size:14px}
.perk{position:absolute;display:flex;align-items:flex-start;gap:9px;font-size:5.8px;line-height:11px;width:240px}
.perk svg{flex:none}
.role-btn{position:absolute;top:260px;width:109px;height:20px;line-height:20px}

/* footer */
.site-footer{position:absolute;left:0;top:1007px;width:710px;height:193px;background:var(--footer)}
.foot-brand{position:absolute;left:78px;top:26px;font-size:24px;font-weight:600;color:var(--orange);letter-spacing:1px}
.social{position:absolute;top:64px;width:18px;height:18px;border:1.2px solid #444;border-radius:50%}
.foot-col{position:absolute;top:22px}
.foot-col h4{font-size:11px;font-weight:400;color:#333;letter-spacing:.3px}
.foot-col li{list-style:none;font-size:6px;color:#555;margin-top:8px}
.contact li{display:flex;gap:7px;align-items:flex-start}
.newsletter p{font-size:6px;color:#555;line-height:14px;margin-top:11px;width:150px}
.news-field{width:140px;height:20px;background:var(--white);border:1px solid #ccc;font-size:5.6px;padding:6px 8px;margin-top:10px}
.news-btn{display:inline-block;margin-top:12px;border:1px solid #333;border-radius:2px;font-size:6px;padding:5px 7px}
.copyright{position:absolute;left:0;top:158px;width:710px;height:35px;border-top:1px solid var(--line);text-align:center;font-size:6px;color:#666;line-height:34px}
</style>
</head>
<body>

<header class="site-header">
  <div class="brand">
    <div class="brand-name">TRAVENOK</div>
    <div class="brand-tag">PROJECT MANAGEMENT CONSULTING</div>
  </div>
  <nav class="main-nav">
    <a href="#" style="left:424px">Professional</a>
    <a href="#" style="left:493px">Employers</a>
    <a href="#" style="left:557px">Sign In</a>
    <a href="#" style="left:608px">Sign Up</a>
  </nav>
</header>

<section class="hero" role="img" aria-label="Dark photo of a hand touching a network of business people icons">
  <h1 class="hero-title center">Hire Top IT Project Management Talents</h1>
  <p class="hero-sub center">Search our network, Shortlist candidates, send interview Requests &amp; fill Positions fast</p>
  <div class="email-field">Your Email Address</div>
  <div class="btn hero-btn">Get Started</div>
  <p class="hero-note">By entering your email address, you agree to our <u>Term &amp; Conditons</u></p>
  <p class="hero-job center">Looking for a job ? <u>upload Resume</u> and let companies send you others</p>
</section>

<nav class="tab-band">
  <span class="tab active" style="left:184px">Our Focus</span>
  <span class="tab" style="left:311px">Why Us?</span>
  <span class="tab" style="left:421px">How it Works</span>
</nav>

<section>
  <h2 class="welcome-title center" style="font-weight:400">Welcome to TRAVENOK</h2>
  <p class="welcome-sub center">Employers pay 25% more for a better FIT Project Manager</p>

  <div class="focus" style="left:69px">
    <div class="focus-ring"><svg width="30" height="26" viewBox="0 0 30 26"><rect x="1" y="1" width="28" height="18" rx="2" fill="#f37122"/><rect x="4" y="4" width="22" height="12" fill="#fff"/><rect x="12" y="19" width="6" height="4" fill="#f37122"/><rect x="8" y="23" width="14" height="2" fill="#f37122"/></svg></div>
    <h3>Project Managers</h3>
    <p>Lorem ipsum dolor sit amet, consectetur adipiscing elit, sed do eiusmod tempor incididunt ut labore et dolore magna aliqua.</p>
  </div>
  <div class="focus" style="left:270px">
    <div class="focus-ring"><svg width="32" height="26" viewBox="0 0 32 26"><circle cx="8" cy="6" r="4" fill="#f37122"/><circle cx="24" cy="6" r="4" fill="#f37122"/><circle cx="16" cy="9" r="5" fill="#f37122"/><path d="M1 18c0-5 4-7 7-7s7 2 7 7z M17 18c0-5 4-7 7-7s7 2 7 7z" fill="#f37122"/><path d="M6 25c0-7 5-10 10-10s10 3 10 10z" fill="#f37122"/></svg></div>
    <h3>PMO Leadership</h3>
    <p>Lorem ipsum dolor sit amet, consectetur adipiscing elit, sed do eiusmod tempor incididunt ut labore et dolore magna aliqua.</p>
  </div>
  <div class="focus" style="left:470px">
    <div class="focus-ring"><svg width="26" height="26" viewBox="0 0 26 26"><rect x="1" y="11" width="6" height="13" fill="#f37122"/><path d="M9 11l5-9c2 0 3 1 3 3l-1 5h7c2 0 3 2 2 3l-2 9c0 1-1 2-3 2H9z" fill="none" stroke="#f37122" stroke-width="2"/></svg></div>
    <h3>PM trainer &amp; Coaches</h3>
    <p>Lorem ipsum dolor sit amet, consectetur adipiscing elit, sed do eiusmod tempor incididunt ut labore et dolore magna aliqua.</p>
  </div>
</section>

<section class="hiring">
  <h2 class="hiring-title center" style="font-weight:400">Hiring Flexiblity</h2>
  <p class="hiring-sub center">Hire an hourly or biring them on as permanent employess</p>
  <div class="divider"></div>

  <h3 class="role-title" style="left:91px;font-weight:400">Contract Roles</h3>
  <div class="perk" style="left:79px;top:152px"><svg width="14" height="14" viewBox="0 0 14 14"><circle cx="7" cy="7" r="5.5" fill="none" stroke="#fff" stroke-width="1.6"/><path d="M7 4v3.5h2.5" stroke="#fff" stroke-width="1.4" fill="none"/></svg><span>Lorem ipsum dolor sit amet, consectetur adipiscing elit, sed do eiusmod tempor incididunt ut labore et dolore magna aliqua.</span></div>
  <div class="perk" style="left:79px;top:191px"><svg width="14" height="14" viewBox="0 0 14 14"><rect x="2.5" y="0.5" width="9" height="13" fill="none" stroke="#fff"/><path d="M4.5 3h1M8.5 3h1M4.5 6h1M8.5 6h1M4.5 9h1M8.5 9h1" stroke="#fff" stroke-width="1.4"/></svg><span style="padding-top:1px">Duis aute irure dolor in reprehenderit in voluptate velit esse cillum</span></div>
  <div class="perk" style="left:79px;top:226px"><svg width="14" height="14" viewBox="0 0 14 14"><path d="M1 2h12L8.5 7.5V13l-3-2V7.5z" fill="#fff"/></svg><span style="padding-top:1px">Duis aute irure dolor in reprehenderit in voluptate velit esse cillum</span></div>
  <div class="btn role-btn" style="left:151px">Search our network</div>

  <h3 class="role-title" style="left:419px;font-weight:400">Permanent Roles</h3>
  <div class="perk" style="left:402px;top:152px"><svg width="14" height="14" viewBox="0 0 14 14"><circle cx="7" cy="7" r="6" fill="#fff"/><path d="M4 4c2 0 2 2 4 2s1 3-1 3M9 10c1 0 2 1 2 2" stroke="#323232" stroke-width="1.3" fill="none"/></svg><span>Lorem ipsum dolor sit amet, consectetur adipiscing elit, sed do eiusmod tempor incididunt ut labore et dolore magna aliqua.</span></div>
  <div class="perk" style="left:402px;top:191px"><svg width="14" height="14" viewBox="0 0 14 14"><path d="M10 3.5C9 2.5 4 2 4 5s6 2 6 5-5 2.5-6 1.5M7 0.5v13" stroke="#fff" stroke-width="1.6" fill="none"/></svg><span style="padding-top:1px">Duis aute irure dolor in reprehenderit in voluptate velit esse cillum</span></div>
  <div class="perk" style="left:402px;top:226px"><svg width="14" height="14" viewBox="0 0 14 14"><rect x="1" y="6" width="3" height="7" fill="#fff"/><path d="M5 6l3-5c1 0 2 1 1.5 2.5L9 6h3.5c1 0 1.5 1 1 2l-1 4c0 .6-.5 1-1.3 1H5z" fill="none" stroke="#fff" stroke-width="1.2"/></svg><span style="padding-top:1px">Duis aute irure dolor in reprehenderit in voluptate velit esse cillum</span></div>
  <div class="btn role-btn" style="left:474px">Contact us</div>
</section>

<footer class="site-footer">
  <div class="foot-brand">TRAVENOK</div>
  <span class="social" style="left:77px"></span>
  <span class="social" style="left:99px"></span>
  <span class="social" style="left:121px"></span>
  <span class="social" style="left:143px"></span>
  <span class="social" style="left:165px"></span>

  <div class="foot-col" style="left:238px">
    <h4>QUICK LINKS</h4>
    <ul><li>Professional</li><li>Employers</li><li>Sign In</li><li>Sign Up</li></ul>
  </div>

  <div class="foot-col contact" style="left:360px">
    <h4>CONTACT US</h4>
    <ul>
      <li><svg width="7" height="7" viewBox="0 0 10 10"><path d="M1 3c0-2 8-2 8 0v1H7V3H3v1H1zM2 5h6l1 4H1z" fill="#666"/></svg>555-014-2290</li>
      <li><svg width="7" height="7" viewBox="0 0 10 10"><rect x="2" y="0.5" width="6" height="3" fill="#666"/><rect x="0.5" y="3.5" width="9" height="4" fill="#666"/><rect x="2" y="6" width="6" height="3.5" fill="#999"/></svg>555-014-3318</li>
      <li><svg width="7" height="7" viewBox="0 0 10 10"><rect x="0.5" y="2" width="9" height="6" fill="none" stroke="#666"/><path d="M0.5 2L5 6l4.5-4" stroke="#666" fill="none"/></svg><u>hello@travenok.example</u></li>
      <li><svg width="7" height="8" viewBox="0 0 10 12"><path d="M5 11.5S1 7 1 4.5a4 4 0 018 0C9 7 5 11.5 5 11.5z" fill="#666"/><circle cx="5" cy="4.5" r="1.5" fill="#ebece4"/></svg><span style="line-height:8px">#2868 Lorem ipsum dolor sit<br>amet, consectetur</span></li>
    </ul>
  </div>

  <div class="foot-col newsletter" style="left:490px;top:27px">
    <h4>SUBSCRIBE NEWSLETTER</h4>
    <p>Enter your email address to receive the latest news our blog.</p>
    <div class="news-field">Email Id</div>
    <span class="news-btn">SUBSCRIBE</span>
  </div>

  <div class="copyright">©2016 travenoktech.example. All Rights Reserved.</div>
</footer>

</body>
</html>
```